Food Trade Show Advertisement

One full-page advertisement sent as a high-resolution .pdf file that is 11.125" w x 14.25" h

Details on the the wording and pictures will be provided
The to include:
Company logo, product photos (to be supplied), wording (to be supplied), Booth number (to be supplied)
Colors - hot pink
Attached is the guidelines for the advertisement

```html
<!DOCTYPE html>
<html lang="en">
<head>
<meta charset="utf-8">
<title>International Food Trade Show – Fava Bloom</title>
<link rel="stylesheet" href="https://fonts.googleapis.com/css2?family=Montserrat:wght@500;600;700&family=Pacifico&display=swap">
<style>
  :root {
    --backdrop: #3d3d3f;
    --hot-pink: #e6147f;
    --deep-pink: #a8155a;
    --soft-pink: #f06aa6;
    --white: #ffffff;
    --photo-light: #f3f3f5;
    --photo-cream: #e9dcc0;
    --grain: #d9b46a;
  }
  * { margin: 0; padding: 0; box-sizing: border-box; }
  html, body {
    width: 1200px; height: 1200px; overflow: hidden;
    background: var(--backdrop);
    font-family: "Montserrat", sans-serif;
  }
  .flyer {
    position: absolute; left: 170px; top: 52px;
    width: 861px; height: 1097px; overflow: hidden;
    background: linear-gradient(150deg, var(--soft-pink) 0%, var(--hot-pink) 45%, #f2559a 70%, var(--hot-pink) 100%);
  }
  .flyer-shapes { position: absolute; inset: 0; }
  .booth-tag {
    position: absolute; left: 618px; top: 40px; width: 243px; height: 30px;
    background: var(--white);
    clip-path: polygon(4% 0, 100% 0, 100% 100%, 0 100%);
    color: var(--hot-pink); font-weight: 600; font-size: 21px;
    display: flex; align-items: center; justify-content: center;
  }
  .brand-badge {
    position: absolute; left: 612px; top: 104px; width: 198px; height: 198px;
    border-radius: 50%; background: var(--white);
    border: 3px solid var(--hot-pink);
    display: flex; align-items: center; justify-content: center;
    color: var(--hot-pink); font-weight: 700; font-size: 30px; text-align: center; line-height: 1.1;
  }
  .product-circle {
    position: absolute; left: 528px; top: 296px; width: 248px; height: 248px;
    border-radius: 50%; border: 3px solid var(--hot-pink);
    background: radial-gradient(ellipse 55% 30% at 50% 55%, var(--grain) 0%, #e8cf9a 55%, var(--photo-light) 100%);
  }
  .headline { position: absolute; left: 0; width: 100%; color: var(--white); }
  .headline-kicker { left: 42px; top: 572px; width: auto; font-weight: 600; font-size: 35px; }
  .headline-title {
    top: 606px; text-align: center; padding-right: 40px;
    font-family: "Pacifico", cursive; font-size: 72px; line-height: 1.3;
    text-shadow: 2px 3px 0 var(--deep-pink);
  }
  .show-dates {
    top: 724px; text-align: center; font-weight: 700; font-size: 38px;
    text-shadow: 0 0 3px var(--deep-pink), 2px 2px 0 var(--deep-pink), -2px -2px 0 var(--deep-pink), 2px -2px 0 var(--deep-pink), -2px 2px 0 var(--deep-pink);
  }
  .show-hours {
    position: absolute; left: 290px; top: 787px; width: 283px; height: 44px;
    border-radius: 22px; background: var(--white);
    color: var(--hot-pink); font-weight: 600; font-size: 30px;
    display: flex; align-items: center; justify-content: center;
  }
  .hours-dot { position: absolute; top: 800px; width: 10px; height: 10px; border-radius: 50%; background: var(--white); }
  .show-location { top: 850px; text-align: center; font-weight: 600; font-size: 20px; }
  .entry-ribbon {
    position: absolute; left: 230px; top: 894px; width: 411px; height: 38px;
    background: var(--white);
    clip-path: polygon(0 0, 100% 0, 96% 50%, 100% 100%, 0 100%, 4% 50%);
    color: var(--hot-pink); font-weight: 600; font-size: 22px;
    display: flex; align-items: center; justify-content: center;
  }
  .contact-phone {
    position: absolute; left: 44px; top: 1012px;
    display: flex; align-items: center; gap: 16px;
    color: var(--white); font-weight: 500; font-size: 31px;
  }
  .organiser {
    position: absolute; left: 660px; top: 950px;
    display: flex; align-items: center; gap: 8px;
    color: var(--white); font-weight: 700; font-size: 18px; letter-spacing: 1px;
  }
  .organiser-dot { width: 22px; height: 22px; border-radius: 50%; background: var(--white); }
</style>
</head>
<body>
  <main class="flyer">
    <svg class="flyer-shapes" width="861" height="1097" viewBox="0 0 861 1097">
      <path d="M0 0 H706 C650 300 470 522 255 514 C140 510 55 470 0 402 Z" fill="var(--photo-light)"/>
      <path d="M706 0 C650 300 470 522 255 514 C140 510 55 470 0 402" fill="none" stroke="var(--hot-pink)" stroke-width="5"/>
      <g role="img" aria-label="Photo of a grey cloth sack spilling fava bean flour">
        <ellipse cx="260" cy="250" rx="230" ry="170" fill="url(#sackTone)"/>
      </g>
      <defs>
        <radialGradient id="sackTone" cx="0.6" cy="0.5" r="0.6">
          <stop offset="0" stop-color="var(--photo-cream)"/>
          <stop offset="0.55" stop-color="#d4d2d0"/>
          <stop offset="1" stop-color="var(--photo-light)"/>
        </radialGradient>
      </defs>
    </svg>

    <div class="booth-tag">Booth No: 123</div>
    <div class="brand-badge">Fava<br>Bloom</div>
    <div class="product-circle" role="img" aria-label="Photo of a pile of textured fava bean protein"></div>

    <p class="headline headline-kicker">International</p>
    <h1 class="headline headline-title">Food Trade Show</h1>
    <p class="headline show-dates">20th June - 27th June</p>
    <span class="hours-dot" style="left:254px"></span>
    <div class="show-hours">10 am - 9 pm</div>
    <span class="hours-dot" style="left:600px"></span>
    <p class="headline show-location">Location: Place Your Location Here</p>
    <div class="entry-ribbon">Free Entry - Free Parking</div>

    <div class="contact-phone">
      <svg width="38" height="38" viewBox="0 0 38 38" aria-hidden="true">
        <circle cx="19" cy="19" r="17" fill="none" stroke="var(--white)" stroke-width="2"/>
        <path d="M13 11 l3 -1 l2 5 l-2 1.5 c1 2.5 3 4.5 5.5 5.5 l1.5 -2 l5 2 l-1 3 c-8 1 -15 -6 -14 -14z" fill="var(--white)"/>
      </svg>
      <span>123 123 123</span>
    </div>

    <div class="organiser"><span class="organiser-dot"></span>MEADOWVALE</div>
  </main>
</body>
</html>
```